Professional violinist needs business cards

I am trying to attract the following jobs:
-private violin lessons (primarily classical)
-performance gigs (weddings, birthday parties, funerals, etc.)
-collaborations with other artists (studio recordings, performances)

I want to communicate that I have a very high standard of excellence for my work, but I also love people and celebrations.
Values/style words I like are:
love, joy, peace, fun, beauty, authenticity, excellence, warmth, refined/sleek, free spirited. If that's too confusing, just ignore :)

I will attach my favorite business card template that I could find on Canva. The lines are supposed to be like a music staff, which I think is really cool, but I also don't want it to look too busy. I like the simple black and white--I think it looks sharp--but I also am open to other ideas. I also have seen business cards with pictures included that looked great, so I attached an image that could be used as well.

I am also attaching a file that I made of my initials that could be used as a logo, but I'm not sure if it should be included.

Information on the card:
-My name (18 letters total)
-"violinist"
-phone number, email, website

Thank you!

```html
<!DOCTYPE html>
<html lang="en">
<head>
<meta charset="utf-8">
<title>Elena Marlowe — Violinist Business Card</title>
<link rel="stylesheet" href="https://fonts.googleapis.com/css2?family=Raleway:wght@400;500;600&display=swap">
<style>
  :root {
    --backdrop: #2a2a2a;
    --card-black: #000000;
    --panel-dark: #1c1c1c;
    --panel-mid: #2e2e2e;
    --gold: #d39e35;
    --white: #ffffff;
    --soft-white: #d8d8d8;
  }
  * { box-sizing: border-box; margin: 0; padding: 0; }
  html, body {
    width: 1200px; height: 900px; overflow: hidden;
    background: var(--backdrop);
    font-family: "Raleway", Arial, sans-serif;
  }
  .canvas {
    position: relative; width: 1200px; height: 900px;
  }
  .card {
    position: absolute; left: 250px; width: 700px; height: 400px;
    background: var(--card-black); overflow: hidden;
    box-shadow: 0 10px 30px rgba(0,0,0,.55);
  }
  .card--front { top: 40px; }
  .card--back { top: 470px; }

  /* Front */
  .staff { position: absolute; inset: 0; }
  .staff line { stroke: var(--gold); stroke-width: 4; }
  .front-name {
    position: absolute; left: 40px; top: 140px;
    color: var(--gold); font-weight: 600; font-size: 78px;
    line-height: 1; letter-spacing: 1px;
    background: var(--card-black); padding: 6px 14px 12px;
  }
  .front-web {
    position: absolute; right: 34px; bottom: 58px;
    color: var(--white); font-size: 15px; letter-spacing: 1.5px;
    background: var(--card-black); padding: 0 6px;
  }

  /* Back */
  .portrait {
    position: absolute; right: 0; top: 0; width: 300px; height: 400px;
    background: linear-gradient(100deg, var(--panel-dark) 0%, var(--panel-mid) 55%, #3a2a20 100%);
  }
  .identity {
    position: absolute; right: 320px; top: 178px; text-align: right;
  }
  .identity__name {
    color: var(--gold); font-weight: 500; font-size: 30px; letter-spacing: .5px;
  }
  .identity__role {
    color: var(--soft-white); font-size: 15px; margin-top: 2px;
  }
  .contacts {
    position: absolute; right: 320px; top: 268px; list-style: none;
  }
  .contacts li {
    display: flex; justify-content: flex-end; align-items: center;
    gap: 12px; color: var(--white); font-size: 17px; line-height: 28px;
  }
  .contacts svg { width: 16px; height: 16px; fill: none; stroke: var(--gold); stroke-width: 1.8; }
</style>
</head>
<body>
<main class="canvas">

  <section class="card card--front" aria-label="Card front">
    <svg class="staff" width="700" height="400" viewBox="0 0 700 400" aria-hidden="true">
      <line x1="0" y1="40" x2="700" y2="40"/>
      <line x1="0" y1="105" x2="700" y2="105"/>
      <line x1="0" y1="170" x2="700" y2="170"/>
      <line x1="0" y1="235" x2="700" y2="235"/>
      <line x1="0" y1="300" x2="700" y2="300"/>
      <line x1="0" y1="365" x2="700" y2="365"/>
    </svg>
    <div class="front-name">Elena Marlowe</div>
    <div class="front-web">www.elenamarlowe.com</div>
  </section>

  <section class="card card--back" aria-label="Card back">
    <div class="portrait" role="img" aria-label="Portrait photo of the violinist in a black dress holding her violin and bow"></div>
    <div class="identity">
      <div class="identity__name">Elena Marlowe</div>
      <div class="identity__role">Violinist</div>
    </div>
    <ul class="contacts">
      <li>012 555 0147
        <svg viewBox="0 0 16 16" aria-hidden="true"><path d="M2 6c0-2 2-3 6-3s6 1 6 3l-3 1-1-2H6L5 7 2 6z"/><rect x="4" y="8" width="8" height="5" rx="1"/></svg>
      </li>
      <li>hello@elenamarlowe.com
        <svg viewBox="0 0 16 16" aria-hidden="true"><rect x="1.5" y="3.5" width="13" height="9"/><path d="M1.5 3.5 8 9l6.5-5.5"/></svg>
      </li>
      <li>www.elenamarlowe.com
        <svg viewBox="0 0 16 16" aria-hidden="true"><circle cx="8" cy="8" r="6.2"/><ellipse cx="8" cy="8" rx="2.6" ry="6.2"/><path d="M1.8 8h12.4"/></svg>
      </li>
    </ul>
  </section>

</main>
</body>
</html>
```